Real Estate - Property Management Prospectus/Brochure

We need a prospectus made up, around 9-10 pages including the cover page pages 3 onwards can be all a similar template happy for the front cover to have lots of black. I would like it to look very classy and futuristic, high end, blacks, silvers and whites, i am specializing in managing high end rental properties. i would like to design to correspond with the logo. I need to be able to email this booklet mostly - and also be able to print and mail out as well. I would like it crisp and clean as well - not to much on a page. Please note - happy for the cover to be simple with the logo added - prefer lots of black and with the other pages - they can all be a similar layout template to make this job easier? My website is www.leasemeridian.com.au and phone is 0418 293 547 email is tmarsh@leasemeridian.com.au
Target Market(s)
Investors
Industry/Entity Type
Real Estate
Requirements
Should not have
- Bright greens or bold colours

```html
<!DOCTYPE html>
<html lang="en">
<head>
<meta charset="utf-8">
<title>Lease Meridian – Introduction</title>
<link rel="stylesheet" href="https://fonts.googleapis.com/css2?family=Roboto+Condensed:wght@300;400&display=swap">
<style>
  :root {
    --ink: #1b1b1b;
    --text: #2a2a2a;
    --tab-black: #1a1a1a;
    --tab-grey: #8c8c8c;
    --page-top: #dedede;
    --page-mid: #f4f4f4;
    --page-white: #ffffff;
    --brand-white: #f2f2f2;
    --city-sky: #f7f8f9;
    --city-haze: #b9c0c6;
    --city-towers: #7d8790;
    --city-shore: #8fa9a8;
  }
  * { margin: 0; padding: 0; box-sizing: border-box; }
  html, body { width: 849px; height: 1200px; overflow: hidden; background: var(--page-white); }
  .page {
    position: relative;
    width: 849px;
    height: 1200px;
    overflow: hidden;
    background: linear-gradient(180deg, var(--page-top) 0%, var(--page-mid) 28%, var(--page-white) 55%);
    font-family: "Roboto Condensed", "Arial Narrow", sans-serif;
  }
  .corner-tab {
    position: absolute;
    top: 0;
    right: 0;
    width: 290px;
    height: 70px;
  }
  .brand {
    position: absolute;
    top: 30px;
    right: 24px;
    display: flex;
    align-items: center;
    gap: 10px;
    color: var(--brand-white);
    font-weight: 400;
    font-size: 15px;
    letter-spacing: 3px;
    text-transform: uppercase;
  }
  .brand-square {
    width: 12px;
    height: 12px;
    background: var(--brand-white);
  }
  .section-title {
    position: absolute;
    left: 97px;
    top: 140px;
    font-weight: 300;
    font-size: 50px;
    color: var(--ink);
    letter-spacing: -0.5px;
  }
  .intro-copy {
    position: absolute;
    left: 97px;
    top: 376px;
    width: 657px;
    font-weight: 400;
    font-size: 18.5px;
    line-height: 31px;
    color: var(--text);
    text-align: justify;
  }
  .intro-copy p + p { margin-top: 17px; }
  .skyline {
    position: absolute;
    left: 0;
    bottom: 0;
    width: 849px;
    height: 520px;
    background: linear-gradient(180deg,
      rgba(255,255,255,0) 0%,
      var(--city-sky) 22%,
      var(--city-haze) 48%,
      var(--city-towers) 72%,
      var(--city-shore) 100%);
  }
</style>
</head>
<body>
<main class="page">
  <svg class="corner-tab" viewBox="0 0 290 70" aria-hidden="true">
    <polygon points="0,0 26,0 92,62 70,62" fill="var(--tab-grey)"/>
    <polygon points="34,0 290,0 290,70 104,70" fill="var(--tab-black)"/>
  </svg>
  <div class="brand"><span class="brand-square"></span>Lease Meridian</div>

  <h1 class="section-title">Introduction</h1>

  <section class="intro-copy">
    <p>Lease Meridian was founded on the belief that investment property management should deliver results that go beyond our client’s expectations.</p>
    <p>Lease Meridian is building a reputation by excelling in every aspect of the property management process, bringing innovation, confidence, and creativeness with an unparalleled commitment to excellence, these values echo in all aspects of Lease Meridian.</p>
  </section>

  <div class="skyline" role="img" aria-label="Coastal city skyline of high-rise towers along a sandy beach and turquoise surf"></div>
</main>
</body>
</html>
```